ORV Web Design Project

I'm looking for a small, friendly,functional, information based website. If you go through the attachments, you would know the nature of the business.
Updates

Hi,

I have uploaded a picture of the CEO, Mr. Delvan Kroth PLMAT member. Please feel free to use it whereever appropriate.

Thanks!

Hello, I have uploaded some references. I like the colours used on the bar and would w

Example of a we page . I like this layout for the inside pages.

I am changing the tabs on my website to:

Home
About us
Services
Contact us

The services tab will have three sub pages:

Immigration
Education
AccommodationAccommodation

Target Market(s)

Young international students willing to come to Canada to study, young international students willing to immigrate to Canada, parents of the students

Industry/Entity Type

Business

Requirements
Must have
• ORV HOME
ABOUT US
CONTACT
SERVICES
TAG LINE

The website should look n feel trendy, smart, current, factual, trustworthy etc....
Nice to have
• I am looking for a bold, attractive, eye catchy home page with less text! Something that makes a statement....
Should not have
• No Clip art, flash animation, no bells n whistles please

```html
<!DOCTYPE html>
<html lang="en">
<head>
<meta charset="utf-8">
<title>ORV – Orvane Business Group</title>
<link rel="stylesheet" href="https://fonts.googleapis.com/css2?family=Barlow+Condensed:wght@500;600&family=Arimo:wght@400;700&family=Source+Sans+3:wght@700&family=Kalam:wght@400&display=swap">
<style>
:root{
  --red:#e8192c;
  --ink:#1d1d1f;
  --card-dark:#232226;
  --grey:#7a7a7a;
  --white:#ffffff;
  --badge-blue:#3f8fd0;
}
*{margin:0;padding:0;box-sizing:border-box}
html,body{width:1200px;height:1018px;overflow:hidden;background:var(--white)}
body{position:relative;font-family:"Arimo",Arial,sans-serif;color:var(--ink)}
.abs{position:absolute}

/* Header */
.brand{left:152px;top:0;width:332px;height:165px;background:linear-gradient(180deg,#f7f7f7,#e6e6e6)}
.brand-ribbon{left:167px;top:165px}
.brand-name{left:262px;top:40px;display:flex;align-items:center;gap:14px;font-family:"Source Sans 3",sans-serif;font-weight:700;font-size:58px;line-height:1;color:var(--ink);letter-spacing:1px}
.brand-mark{width:30px;height:30px;background:var(--red)}
.brand-full{left:166px;top:106px;font-family:"Source Sans 3",sans-serif;font-weight:700;font-size:29px;color:var(--grey);letter-spacing:-.3px;white-space:nowrap}

.social{left:966px;top:13px;display:flex;gap:8px}
.social span{width:14px;height:14px;border-radius:3px;background:#a3a3a3}

.nav{left:0;top:0;list-style:none}
.nav li{position:absolute;top:74px;white-space:nowrap}
.nav b{display:block;font-family:"Barlow Condensed",sans-serif;font-weight:600;font-size:26px;line-height:26px;color:var(--ink);letter-spacing:-.3px}
.nav small{display:block;font-size:11px;color:#555;margin-top:3px}
.nav .active b,.nav .active small{color:var(--red)}
.nav .active::before{content:"";position:absolute;left:0;top:-38px;width:46px;height:30px;
  background:radial-gradient(circle at 23px 6px,var(--red) 5px,transparent 5.5px),linear-gradient(var(--ink),var(--ink)) 0 26px/46px 4px no-repeat}
.nav-divider{top:72px;width:0;height:44px;border-left:1px dotted #c9c9c9}

/* Hero */
.hero{left:57px;top:165px;width:1119px;height:725px;
  background:
    linear-gradient(90deg,#fff 0,rgba(255,255,255,0) 7%,rgba(255,255,255,0) 93%,#fff 100%),
    linear-gradient(180deg,rgba(255,255,255,0) 70%,#fff 100%),
    linear-gradient(120deg,#d9c8d0 0%,#c58aa8 25%,#3a3f7a 45%,#c7a58f 60%,#d14f91 75%,#e7d9e2 100%)}
.tagline{left:159px;top:412px;width:558px;height:52px;background:var(--red);color:var(--white);
  font-family:"Kalam",cursive;font-size:38px;line-height:52px;padding-left:30px}
.badge{left:476px;top:466px;width:558px;height:75px;background:var(--white);display:flex;align-items:center;padding-left:36px;gap:18px}
.badge-circle{width:52px;height:52px;border-radius:50%;background:var(--badge-blue)}
.badge-bar{width:360px;height:28px;background:#d8d8d8}
.pager{top:557px;width:10px;height:10px;border-radius:50%;background:var(--red)}

.cards{left:159px;top:581px;display:flex;gap:4px}
.card{width:214px;height:218px;padding:14px 14px 0 18px;color:var(--white);position:relative;overflow:hidden}
.card.red{background:var(--red)}
.card.dark{background:var(--card-dark)}
.card h2{font-family:"Barlow Condensed",sans-serif;font-weight:600;font-size:33px;line-height:38px;letter-spacing:-.5px;margin-bottom:12px;white-space:nowrap}
.card h2 small{font-size:21px}
.card p{font-size:11px;line-height:16.2px}
.card ul{list-style:none;font-size:11px}
.card li{height:25px;line-height:16px;border-bottom:1px solid rgba(255,255,255,.12);white-space:nowrap}
.card .more{position:absolute;left:18px;bottom:10px;font-size:11px;font-weight:700;color:var(--white);text-decoration:none}

.slogan{left:183px;top:822px;font-family:"Barlow Condensed",sans-serif;font-weight:600;font-size:35px;line-height:40px;color:#2a2a2a;letter-spacing:-.5px;white-space:nowrap}
.divider{left:652px;top:824px;width:1px;height:36px;background:#cfcfcf}
.phone-icon{left:676px;top:821px}
.call{left:724px;top:830px;font-family:"Barlow Condensed",sans-serif;font-weight:600;font-size:21px;line-height:24px;color:#555;white-space:nowrap}
.call-number{left:831px;top:821px;font-family:"Barlow Condensed",sans-serif;font-weight:600;font-size:36px;line-height:40px;color:var(--red);letter-spacing:-.3px;white-space:nowrap}

/* Footer */
.footer{left:159px;top:900px;width:784px;height:43px;background:var(--red);display:flex;align-items:center;padding-left:26px;color:var(--white);font-size:12px}
.footer strong{margin-right:22px}
.signup{position:absolute;right:16px;top:7px;width:236px;height:31px;background:var(--card-dark);display:flex;align-items:center;justify-content:space-between;padding:0 4px 0 10px;font-size:12px}
.signup button{font-family:"Barlow Condensed",sans-serif;font-weight:600;font-size:17px;background:#ececec;border:none;color:var(--ink);padding:0 10px;height:24px}
.footer-brand{left:958px;top:908px;display:flex;align-items:center;gap:5px;font-family:"Source Sans 3",sans-serif;font-weight:700;font-size:24px;color:var(--ink)}
.footer-brand i{width:11px;height:11px;background:var(--red)}
</style>
</head>
<body>

<header>
  <div class="abs brand"></div>
  <svg class="abs brand-ribbon" width="302" height="17" aria-hidden="true"><polygon points="0,0 302,0 290,17 12,17" fill="#c8c8c8"/></svg>
  <div class="abs brand-name">ORV<span class="brand-mark"></span></div>
  <div class="abs brand-full">Orvane Business Group</div>

  <div class="abs social" role="img" aria-label="Social links"><span></span><span></span><span></span></div>

  <ul class="abs nav">
    <li class="active" style="left:509px"><b>HOME</b><small>Start Here</small></li>
    <li style="left:610px"><b>ABOUT</b><small>Our Company</small></li>
    <li style="left:708px"><b>SERVICES</b><small>What We Do</small></li>
    <li style="left:826px"><b>PARTNERS</b><small>Program</small></li>
    <li style="left:955px"><b>CONTACT</b><small>Reach Us</small></li>
  </ul>
  <span class="abs nav-divider" style="left:583px"></span>
  <span class="abs nav-divider" style="left:690px"></span>
  <span class="abs nav-divider" style="left:801px"></span>
  <span class="abs nav-divider" style="left:930px"></span>
</header>

<main>
  <div class="abs hero" role="img" aria-label="Photo of international graduates in caps and gowns celebrating"></div>
  <div class="abs tagline">Taking you onwards……</div>
  <div class="abs badge" role="img" aria-label="Regulatory council membership badge"><span class="badge-circle"></span><span class="badge-bar"></span></div>
  <span class="abs pager" style="left:249px"></span>
  <span class="abs pager" style="left:473px;background:#3b3b55"></span>
  <span class="abs pager" style="left:695px"></span>

  <section class="abs cards">
    <article class="card red">
      <h2>What We Do</h2>
      <p>Lorem ipsum dolor sit amet, consectetuer adipiscing elit, sed diam nonummy nibh euismod tincidunt ut laoreet dolore magna aliquam erat volutpat. Ut wisi enim ad minim veniam, quis nostrud exerci tation ullamcorper..</p>
      <a class="more" href="#">Read More… ›</a>
    </article>
    <article class="card dark">
      <h2>Who We Are</h2>
      <p>Lorem ipsum dolor sit amet, consectetuer adipiscing elit, sed diam nonummy nibh euismod tincidunt ut laoreet dolore magna aliquam erat volutpat. Ut wisi enim ad minim veniam, quis nostrud exerci tation ullamcorper..</p>
      <a class="more" href="#">Read More… ›</a>
    </article>
    <article class="card red">
      <h2>What We Offer</h2>
      <ul>
        <li>Lorem ipsum dolor sit amet,</li>
        <li>Consectetuer adipiscing elit, sed</li>
        <li>Diam nonummy nibh euismod</li>
        <li>Tincidunt ut laoreet dolore magna</li>
        <li>Aliquam erat volutpat ut wisi enim ad</li>
      </ul>
      <a class="more" href="#">Read More… ›</a>
    </article>
    <article class="card dark">
      <h2>Where <small>We Have Been</small></h2>
      <ul>
        <li>Lorem ipsum dolor sit amet,</li>
        <li>Consectetuer adipiscing elit, sed</li>
        <li>Diam nonummy nibh euismod</li>
        <li>Tincidunt ut laoreet dolore magna</li>
        <li>Aliquam erat volutpat ut wisi enim ad</li>
      </ul>
      <a class="more" href="#">Read More… ›</a>
    </article>
  </section>

  <p class="abs slogan">we will show you the way of success!</p>
  <span class="abs divider"></span>
  <svg class="abs phone-icon" width="36" height="42" viewBox="0 0 24 24" aria-hidden="true"><path fill="#e8192c" d="M6.6 10.8c1.4 2.8 3.8 5.1 6.6 6.6l2.2-2.2c.3-.3.7-.4 1-.2 1.1.4 2.3.6 3.6.6.6 0 1 .4 1 1V20c0 .6-.4 1-1 1C10.6 21 3 13.4 3 4c0-.6.4-1 1-1h3.5c.6 0 1 .4 1 1 0 1.3.2 2.5.6 3.6.1.3 0 .7-.2 1z"/></svg>
  <p class="abs call">Call Us Today</p>
  <p class="abs call-number">(800) 555 0142</p>
</main>

<footer>
  <div class="abs footer">
    <strong>© 2013 Orvane Business Group. All Rights Reserved</strong>
    <span>Privacy Policy &nbsp;- Term of use</span>
    <div class="signup"><span>Email Address</span><button type="button">SIGN UP</button></div>
  </div>
  <div class="abs footer-brand">ORV<i></i></div>
</footer>

</body>
</html>
```